Brake Test Training for Coal Mining

We offer Brake Test Training for Coal Mine workers. It's a legislative requirement that workers who are tasked with performing brake testing have certain competencies to do so. We test Light Vehicles and trailers, Heavy Vehicles and Mobile Mining Equipment like Graders, Scrapers and Dump Trucks.

```html
<!DOCTYPE html>
<html lang="en">
<head>
<meta charset="utf-8">
<title>Brake Test Training for Coal Mining</title>
<link rel="stylesheet" href="https://fonts.googleapis.com/css2?family=Inter+Tight:wght@600;700;800;900&display=swap">
<style>
  :root {
    --navy: #1f2f6e;
    --navy-deep: #16245a;
    --yellow: #ffcb05;
    --white: #ffffff;
    --black: #0b0b0b;
    --amber: #b36a1c;
    --amber-dark: #4a2b10;
  }
  html, body { margin: 0; padding: 0; overflow: hidden; background: var(--navy); }
  .banner {
    position: relative;
    width: 1200px;
    height: 588px;
    overflow: hidden;
    font-family: "Inter Tight", "Arial Narrow", sans-serif;
    background: var(--navy);
  }
  .scene-backdrop {
    position: absolute; left: 0; top: 0; width: 1200px; height: 432px;
    background:
      radial-gradient(ellipse 260px 200px at 720px 190px, rgba(90,110,170,.55), transparent 70%),
      linear-gradient(180deg, #233777 0%, #2c4288 55%, #33498f 100%);
  }
  .truck-photo {
    position: absolute; left: 782px; top: 0; width: 418px; height: 432px;
    background:
      radial-gradient(ellipse 160px 120px at 250px 170px, rgba(255,190,90,.85), transparent 70%),
      linear-gradient(160deg, rgba(50,60,110,0) 0%, var(--amber) 35%, #7a4716 65%, var(--amber-dark) 100%);
    -webkit-mask-image: linear-gradient(90deg, transparent 0, #000 60px);
            mask-image: linear-gradient(90deg, transparent 0, #000 60px);
  }
  .brand {
    position: absolute; left: 94px; top: 48px;
    display: flex; align-items: center; gap: 18px;
    color: var(--white); font-weight: 800; font-size: 22px; letter-spacing: .03em;
    text-transform: uppercase; line-height: 26px;
  }
  .brand-dot { width: 62px; height: 62px; border-radius: 50%; border: 3px solid var(--white); box-sizing: border-box; flex: none; }
  .web-tag {
    position: absolute; left: 410px; top: 52px; width: 413px; height: 66px;
    background: linear-gradient(90deg, var(--yellow) 0%, var(--yellow) 62%, rgba(255,203,5,0) 100%);
    display: flex; align-items: center; gap: 12px; padding-left: 15px; box-sizing: border-box;
    color: var(--navy-deep); font-weight: 800; font-size: 31px; letter-spacing: -.02em;
  }
  .web-tag svg { width: 40px; height: 40px; flex: none; }
  .headline {
    position: absolute; left: 74px; top: 142px; margin: 0;
    font-weight: 900; font-size: 84px; line-height: 70px; letter-spacing: -.035em;
    text-transform: uppercase; color: var(--white);
  }
  .headline .accent { color: var(--yellow); display: block; }
  .intro {
    position: absolute; left: 90px; top: 312px; margin: 0;
    color: var(--white); font-weight: 700; font-size: 21.5px; line-height: 29.5px;
    letter-spacing: -.02em; text-transform: uppercase;
  }
  .contact-band { position: absolute; left: 0; top: 432px; width: 1200px; height: 156px; }
  .phone-badge {
    position: absolute; left: 48px; top: 469px; width: 80px; height: 80px; border-radius: 50%;
    background: var(--yellow); display: flex; align-items: center; justify-content: center;
  }
  .phone-badge svg { width: 42px; height: 42px; }
  .phone-number {
    position: absolute; left: 154px; top: 464px;
    color: var(--navy); font-weight: 900; font-size: 84px; line-height: 1; letter-spacing: -.045em;
  }
  .apply-cta {
    position: absolute; left: 790px; top: 478px;
    color: var(--black); font-weight: 900; font-size: 61px; line-height: 1; letter-spacing: -.035em;
  }
</style>
</head>
<body>
<main class="banner">
  <div class="scene-backdrop" role="img" aria-label="Night city skyline with a mine worker in a hard hat, tinted blue"></div>
  <div class="truck-photo" role="img" aria-label="Orange heavy haul truck front view"></div>

  <div class="brand"><span class="brand-dot"></span><span>Summit<br>Operator Training</span></div>

  <div class="web-tag">
    <svg viewBox="0 0 40 40" fill="none" stroke="#16245a" stroke-width="3">
      <circle cx="20" cy="20" r="17"/>
      <ellipse cx="20" cy="20" rx="7.5" ry="17"/>
      <line x1="3" y1="20" x2="37" y2="20"/>
      <path d="M6 11h28M6 29h28"/>
    </svg>
    www.summitot.net.au
  </div>

  <h1 class="headline">Your Trusted<span class="accent">Training Partner</span></h1>

  <p class="intro">We offer brake test training for coal mine workers. We<br>test light vehicles and trailers, heavy vehicles and mobile<br>mining equipment like graders, scrapers and dump trucks.</p>

  <svg class="contact-band" viewBox="0 0 1200 156" preserveAspectRatio="none">
    <polygon points="0,0 730,0 676,156 0,156" fill="#ffffff"/>
    <polygon points="724,0 738,0 684,156 670,156" fill="#1f2f6e"/>
    <polygon points="738,0 1200,0 1200,156 694,156" fill="#ffcb05"/>
  </svg>

  <div class="phone-badge">
    <svg viewBox="0 0 24 24" fill="#ffffff">
      <path d="M6.6 10.8a15.1 15.1 0 0 0 6.6 6.6l2.2-2.2a1 1 0 0 1 1-.25 11.4 11.4 0 0 0 3.6.57 1 1 0 0 1 1 1V20a1 1 0 0 1-1 1A17 17 0 0 1 3 4a1 1 0 0 1 1-1h3.5a1 1 0 0 1 1 1c0 1.25.2 2.450.57 3.57a1 1 0 0 1-.25 1z"/>
    </svg>
  </div>
  <div class="phone-number">1300 555 019</div>
  <div class="apply-cta">APPLY NOW</div>
</main>
</body>
</html>
```